BWP Business Card

A double sided business card based on your "Brindlewood Partners Ltd" Logo. To use the "BWP" logo on 1 side and the full company logo on the reverse.

Detials to be included:

Name: Tomas Wheeler
Postion: Consultant Orthotist & Expert Witness
T: +44 (0) 7700 938271
F: +44 (0) 7654 8820

```html
<!DOCTYPE html>
<html lang="en">
<head>
<meta charset="utf-8">
<title>BWP Business Card</title>
<link href="https://fonts.googleapis.com/css2?family=Tinos:wght@400;700&display=swap" rel="stylesheet">
<style>
  :root {
    --navy: #0f3a73;
    --grey: #9a9a9c;
    --line: #b9b9bb;
    --ink: #2b2b2e;
    --paper: #ffffff;
    --backdrop: #e9e9ef;
  }
  * { box-sizing: border-box; margin: 0; padding: 0; }
  html, body { width: 1200px; height: 987px; overflow: hidden; background: var(--backdrop); }
  .canvas { position: relative; width: 1200px; height: 987px; }
  .card {
    position: absolute; left: 240px; width: 720px; height: 436px;
    background: var(--paper); border-radius: 26px; overflow: hidden;
    box-shadow: 0 6px 18px rgba(0,0,0,.12);
  }
  .card--back { top: 38px; }
  .card--front { top: 513px; }

  /* back side */
  .brand { position: absolute; left: 120px; top: 150px; display: flex; align-items: center; }
  .brand__square { width: 96px; height: 96px; background: var(--navy); flex: none; }
  .brand__divider { width: 1px; height: 130px; background: var(--line); margin: 0 30px; }
  .brand__name {
    font-family: "Tinos", serif; font-weight: 700; font-size: 42px;
    line-height: 1.08; color: var(--navy);
  }

  /* front side */
  .front__brand { position: absolute; left: 60px; top: 88px; display: flex; align-items: center; gap: 16px; }
  .front__square { width: 40px; height: 40px; background: var(--navy); flex: none; }
  .front__name {
    font-family: "Tinos", serif; font-weight: 700; font-size: 66px;
    line-height: 1; color: var(--navy);
  }
  .front__divider { position: absolute; left: 318px; top: 70px; width: 1px; height: 150px; background: var(--line); }
  .contact { position: absolute; left: 342px; top: 74px; font-family: "Tinos", serif; }
  .contact__name { font-weight: 700; font-size: 22px; color: var(--navy); }
  .contact__role { font-size: 15px; color: var(--grey); margin-top: 2px; }
  .contact__list { list-style: none; margin-top: 14px; }
  .contact__item { display: flex; align-items: center; gap: 9px; font-size: 16.5px; color: var(--ink); line-height: 26px; }
  .contact__item svg { width: 15px; height: 15px; fill: var(--navy); flex: none; }
  .swoosh { position: absolute; left: 0; top: 0; }
  .address {
    position: absolute; left: 26px; top: 330px;
    font-family: "Tinos", serif; font-size: 15px; color: var(--paper);
    transform: rotate(9deg); transform-origin: left top;
  }
</style>
</head>
<body>
<div class="canvas">

  <section class="card card--back">
    <div class="brand">
      <div class="brand__square"></div>
      <div class="brand__divider"></div>
      <div class="brand__name">Brindlewood<br>Partners Ltd</div>
    </div>
  </section>

  <section class="card card--front">
    <svg class="swoosh" width="720" height="436" viewBox="0 0 720 436">
      <path d="M0 232 C170 240 330 300 450 370 C540 420 640 436 720 436 L720 436 L0 436 Z" fill="var(--grey)"/>
      <path d="M0 248 C170 258 330 316 446 382 C536 428 640 436 720 436 L720 436 L0 436 Z" fill="var(--paper)"/>
      <path d="M0 262 C160 276 300 336 400 392 C470 428 560 436 720 436 L0 436 Z" fill="var(--navy)"/>
    </svg>
    <div class="front__brand">
      <div class="front__square"></div>
      <div class="front__name">BWP</div>
    </div>
    <div class="front__divider"></div>
    <div class="contact">
      <div class="contact__name">Tomas Wheeler</div>
      <div class="contact__role">Consultant Orthotist &amp; Expert Witness</div>
      <ul class="contact__list">
        <li class="contact__item">
          <svg viewBox="0 0 24 24"><path d="M6.6 10.8a15 15 0 0 0 6.6 6.6l2.2-2.2c.3-.3.7-.4 1-.2 1.1.4 2.3.6 3.6.6.6 0 1 .4 1 1V20c0 .6-.4 1-1 1A17 17 0 0 1 3 4c0-.6.4-1 1-1h3.5c.6 0 1 .4 1 1 0 1.3.2 2.5.6 3.6.1.3 0 .7-.2 1z"/></svg>
          +44 (0) 7700 938271
        </li>
        <li class="contact__item">
          <svg viewBox="0 0 24 24"><path d="M6 3h9v5H6zM4 9h16a2 2 0 0 1 2 2v7h-4v3H6v-3H2v-7a2 2 0 0 1 2-2zm4 8v2h8v-2z"/></svg>
          +44 (0) 7654 8820
        </li>
        <li class="contact__item">
          <svg viewBox="0 0 24 24"><path d="M3 5h18a1 1 0 0 1 1 1v12a1 1 0 0 1-1 1H3a1 1 0 0 1-1-1V6a1 1 0 0 1 1-1zm1 2v.4l8 5 8-5V7l-8 5z"/></svg>
          tomas@brindlewoodpartners.co.uk
        </li>
      </ul>
    </div>
    <div class="address">18 Marlow Close, Kingsford, Surrey, KT9 4RX</div>
  </section>

</div>
</body>
</html>
```